Book cover

I need a cover for a my 3rd book that kinda goes with my brand (my previous book. The name of my first book - "Turbulence Behind the Yoke" Hidden Strain Inside Modern Cockpits: A Guide for Travelers". In the same style I need my third book - NO HARBOR" to stand out. I need a bolder, less whimsy cover, less playful. So can we use some of the same elements to stay consistent in this book cover. Perhaps use text to envoke emotions. This is the back cover so far (see below attachemnent)

Hello,
Subject: Cover Direction & Brand Consistency

Hi everyone,

Here’s my honest take: I don’t think the current execution fully reflects my brand yet. What I’m wondering is whether we can bring more continuity across my books—borrowing elements from my first and second covers to inform this third one. Think of how authors like Dorian Welk maintain a recognizable style across their work. That consistency builds trust and signals authority before a reader even opens the book. Design choices like this matter more than we realize.

I’ve attached a cover I came across on Brindlemart that reminded me of Option 5 and feels aligned with where you’re headed. One thought: could we experiment with introducing a crack—or cracks—into the word HARBOR itself? Maybe put the title "NO HARBOR" at the edge of the cover vertically?

Curious to hear your thoughts and how you see this evolving.
P.s. Is there away to attach an idea?

NO HARBOR: Restoring Quiet Edges in a Culture that Praises Hurry

```html
<!DOCTYPE html>
<html lang="en">
<head>
<meta charset="utf-8">
<title>No Harbor — Book Cover Spread</title>
<link href="https://fonts.googleapis.com/css2?family=Marcellus+SC&family=Montserrat:wght@400;700&family=Roboto:wght@300;400&family=Roboto+Condensed:wght@400&display=swap" rel="stylesheet">
<style>
  :root {
    --stage: #b3b3b3;
    --navy-top: #18212e;
    --navy-bottom: #080b10;
    --teal: #12a8a8;
    --white: #ffffff;
    --pink: #f25cd0;
    --coral: #ff5a6e;
    --sky-teal: #1f6f80;
    --sky-pink: #c94a74;
    --dusk: #3a2838;
    --avatar-ring-a: #1b9fc4;
    --avatar-ring-b: #1565c0;
    --logo-a: #1a8fd0;
    --logo-b: #0fb0b5;
  }
  * { box-sizing: border-box; margin: 0; padding: 0; }
  html, body {
    width: 1200px; height: 1200px; overflow: hidden;
    background: var(--stage);
  }
  .spread {
    position: absolute; left: 88px; top: 223px;
    width: 1025px; height: 754px;
    display: flex;
    box-shadow: -6px 8px 14px rgba(0,0,0,0.35);
  }
  /* Back cover */
  .back-cover {
    position: relative; width: 512px; height: 100%;
    background: linear-gradient(180deg, var(--navy-top) 0%, #111821 60%, var(--navy-bottom) 100%);
    color: var(--white);
    font-family: "Roboto", sans-serif;
  }
  .back-hook {
    position: absolute; left: 48px; top: 56px; width: 418px;
    text-align: center; color: var(--teal);
    font-size: 12.4px; line-height: 15px; font-weight: 400;
  }
  .back-blurb {
    position: absolute; left: 48px; top: 119px; width: 418px;
    font-size: 12.5px; line-height: 15.1px; text-align: justify;
  }
  .author-avatar {
    position: absolute; left: 210px; top: 454px;
    width: 92px; height: 92px; border-radius: 50%;
    padding: 3px;
    background: linear-gradient(135deg, var(--avatar-ring-a), var(--avatar-ring-b));
  }
  .author-avatar .photo {
    width: 100%; height: 100%; border-radius: 50%;
    background: radial-gradient(circle at 50% 40%, #8b8f96 0%, #3e434c 55%, #1b2029 100%);
  }
  .author-bio {
    position: absolute; left: 48px; top: 555px; width: 418px;
    font-size: 12.5px; line-height: 15.1px; text-align: justify;
  }
  .publisher-mark {
    position: absolute; left: 48px; top: 619px;
  }
  .publisher-mark .square {
    width: 53px; height: 53px;
    background: linear-gradient(135deg, var(--logo-a), var(--logo-b));
  }
  .publisher-mark .label {
    margin-top: 4px;
    font-family: "Roboto Condensed", sans-serif;
    font-size: 13px; line-height: 15.5px;
  }
  .price {
    position: absolute; left: 405px; top: 666px;
    font-family: "Roboto Condensed", sans-serif;
    font-size: 15px; line-height: 20.5px;
  }
  /* Front cover */
  .front-cover {
    position: relative; width: 513px; height: 100%; overflow: hidden;
    background: #121a24;
  }
  .front-scene {
    position: absolute; inset: 0;
    background:
      linear-gradient(180deg, rgba(18,26,36,0) 50%, rgba(18,26,36,0.85) 72%, #121a24 85%),
      radial-gradient(ellipse at 60% 35%, var(--sky-pink) 0%, rgba(201,74,116,0) 45%),
      linear-gradient(180deg, #0f2430 0%, var(--sky-teal) 22%, #5b3a5c 48%, var(--dusk) 62%, #1e1f2c 75%);
  }
  .title {
    position: absolute; left: 0; width: 100%; top: 488px;
    text-align: center;
    font-family: "Marcellus SC", serif; font-weight: 400;
    font-size: 78px; line-height: 1; letter-spacing: 1px;
    color: var(--white);
  }
  .subtitle {
    position: absolute; left: 57px; top: 568px;
    padding-left: 12px;
    border-left: 1.5px solid var(--pink);
    font-family: "Montserrat", sans-serif; font-weight: 400;
    font-size: 25px; line-height: 30px; text-transform: uppercase;
    color: var(--pink);
  }
  .subtitle .lead {
    background: linear-gradient(90deg, var(--pink) 0%, var(--coral) 100%);
    -webkit-background-clip: text; background-clip: text; color: transparent;
  }
  .author-name {
    position: absolute; left: 0; width: 100%; top: 686px;
    text-align: center;
    font-family: "Montserrat", sans-serif; font-weight: 700;
    font-size: 14.5px; color: var(--white); letter-spacing: 0.2px;
  }
</style>
</head>
<body>
  <main class="spread">
    <section class="back-cover">
      <p class="back-hook">Women have been told we could do and be anything … and we can.<br>What’s rarely mentioned is the toll on our health, relationships, and overall wellbeing.</p>
      <div class="back-blurb">
        <p>Are you the woman who holds it all together—crushing deadlines, leading teams, raising a family—while quietly unraveling inside? Yes, you are competent and capable. You’ve simply been carrying more than you were ever meant to for too long.</p>
        <p>No Harbor offers a different way forward. Drawn from decades of experience flying commercial aircraft and championing women's health, retired Captain Maren Ostrowe reveals the missing skill most high-achieving women were never taught: restoring your quiet edges in a culture that praises hurry. This vital buffer not only enables recovery after near-collapse, but also prevents you from reaching the breaking point of exhaustion.</p>
        <p>You will learn about the centuries-old mindset when humans first became cogs in the machine, the science of burnout and brain rewiring, the psychology driving us to push limits, and the cultural systems rigged against women. Discover how to spot the three stages of depletion before they ground you. Through self-assessment tools and actionable practices, the author guides us back home to ourselves by offering a roadmap to rebuild our strength, reconnect with joy and purpose, and redefine success to include true wellbeing.</p>
        <p>You don’t need to crash to earn a soft landing. Buckle up! No Harbor is your wakeup call to fly lighter and higher than you ever imagined.</p>
      </div>
      <div class="author-avatar"><div class="photo" role="img" aria-label="Portrait of the author in pilot uniform"></div></div>
      <p class="author-bio">Maren Ostrowe is a speaker, consultant, and founder of the Skyward Wellness Collective. With over 10,000 flight hours, she now empowers women to successfully lead without losing themselves.</p>
      <div class="publisher-mark">
        <div class="square"></div>
        <p class="label">SAMPLE<br>LOGO HERE</p>
      </div>
      <p class="price">US $99.99<br>CA $99.99</p>
    </section>
    <section class="front-cover">
      <div class="front-scene" role="img" aria-label="Jet airliner landing toward the viewer under a dramatic teal and pink sunset sky over a stadium runway"></div>
      <h1 class="title">No Harbor</h1>
      <p class="subtitle"><span class="lead">Restoring quiet edges</span><br>in a culture that<br>praises hurry</p>
      <p class="author-name">CAPT. MAREN OSTROWE</p>
    </section>
  </main>
</body>
</html>
```